IT Company requires new Business Card design.

Over the years we have had a few different business card designs. We are now due for new cards across the board for all staff. We felt this would be a good time to start fresh with a new design. Our traditional card simply had our details on the front, and a list of services on the back. We don't particularly need the list of services, we have had cards where the only thing on the rear of the card was our logo.
Feel free to be creative, we would like our tag line "Complete IT Management" to appear at some point, doesn't necessarily have to be with the logo.
I have attached samples and drafts of various previous cards we have used over the years.

```html
<!DOCTYPE html>
<html lang="en">
<head>
<meta charset="utf-8">
<title>Ridgeway Networks – Business Card</title>
<link href="https://fonts.googleapis.com/css2?family=Open+Sans:wght@400;600;700;800&display=swap" rel="stylesheet">
<style>
  :root {
    --backdrop: #e4e4e2;
    --card: #ffffff;
    --slate: #5f6b75;
    --charcoal: #3b3b3b;
    --ink: #454545;
    --rule: #8a8a8a;
  }
  * { margin: 0; padding: 0; box-sizing: border-box; }
  html, body {
    width: 1034px; height: 1200px; overflow: hidden;
    background: var(--backdrop);
    font-family: "Open Sans", Arial, sans-serif;
    color: var(--ink);
  }
  .canvas { position: relative; width: 1034px; height: 1200px; }
  .card {
    position: absolute; left: 74px; width: 902px;
    background: var(--card); border-radius: 34px; overflow: hidden;
    box-shadow: 0 4px 14px rgba(0,0,0,.18);
  }
  .card--front { top: 69px; height: 511px; }
  .card--back { top: 631px; height: 513px; }

  .brand { position: absolute; display: flex; align-items: center; }
  .brand__square { background: var(--slate); flex: none; }
  .brand__name {
    color: var(--slate); font-weight: 800; text-transform: uppercase;
    line-height: .95; letter-spacing: .5px;
  }
  .card--front .brand { left: 170px; top: 42px; gap: 30px; }
  .card--front .brand__square { width: 112px; height: 112px; }
  .card--front .brand__name { font-size: 62px; }

  .holder {
    position: absolute; right: 524px; top: 262px; text-align: right;
  }
  .holder__name { font-size: 26px; font-weight: 700; color: var(--slate); line-height: 1.2; }
  .holder__role { font-size: 21px; line-height: 1.3; margin-bottom: 14px; }
  .holder__address { font-size: 21px; line-height: 1.5; }

  .divider {
    position: absolute; left: 398px; top: 248px; width: 1px; height: 155px;
    background: var(--rule);
  }

  .contacts { position: absolute; left: 422px; top: 248px; list-style: none; }
  .contacts li {
    display: flex; align-items: center; gap: 12px;
    font-size: 21px; height: 35px;
  }
  .contacts svg { width: 20px; height: 20px; fill: var(--slate); flex: none; }

  .footer-rule {
    position: absolute; left: 0; right: 0; bottom: 52px; height: 6px;
    background: var(--charcoal);
  }
  .footer-band {
    position: absolute; left: 0; right: 0; bottom: 0; height: 44px;
    background: var(--slate);
    display: flex; align-items: center; justify-content: flex-end;
    padding-right: 50px;
  }
  .tagline {
    color: #fff; font-size: 20px; letter-spacing: 4px; font-weight: 400;
  }

  .card--back .brand {
    left: 0; right: 0; top: 110px; flex-direction: column; gap: 34px;
  }
  .card--back .brand__square { width: 130px; height: 130px; }
  .card--back .brand__name { font-size: 60px; text-align: center; }
  .web {
    position: absolute; left: 0; right: 0; top: 463px; text-align: center;
    font-size: 27px; letter-spacing: 2.5px; color: var(--charcoal);
  }
</style>
</head>
<body>
<main class="canvas">

  <section class="card card--front" aria-label="Card front">
    <div class="brand">
      <span class="brand__square"></span>
      <span class="brand__name">Ridgeway<br>Networks</span>
    </div>

    <div class="holder">
      <p class="holder__name">Daniel Hart</p>
      <p class="holder__role">Operation Manager</p>
      <p class="holder__address">Unit 4 18 Harbour Road<br>Bibra Lake WA 6163</p>
    </div>

    <span class="divider"></span>

    <ul class="contacts">
      <li><svg viewBox="0 0 20 20"><circle cx="10" cy="10" r="9" fill="none" stroke="#5f6b75" stroke-width="1.6"/><path d="M6.5 5.5l2 0 .8 2.5-1.3 1c.6 1.3 1.5 2.2 2.8 2.8l1-1.3 2.5.8v2c-4.5.4-8.3-3.4-7.8-7.8z"/></svg>08 9552 4180</li>
      <li><svg viewBox="0 0 20 20"><rect x="5" y="1.5" width="10" height="17" rx="1.5"/><rect x="6.8" y="3.5" width="6.4" height="5.5" fill="#fff"/><rect x="7" y="11" width="6" height="5" fill="#fff" opacity=".6"/></svg>0412 708 936</li>
      <li><svg viewBox="0 0 20 20"><rect x="5.5" y="2" width="9" height="6" fill="none" stroke="#5f6b75" stroke-width="1.6"/><rect x="2" y="8" width="16" height="8" rx="1.5"/><rect x="5.5" y="13" width="9" height="5"/></svg>08 9552 4180</li>
      <li><svg viewBox="0 0 20 20"><rect x="2" y="4.5" width="16" height="11" rx="1.5"/><path d="M2.5 5.5l7.5 5.5 7.5-5.5" fill="none" stroke="#fff" stroke-width="1.5"/></svg>daniel@ridgewaynetworks.com.au</li>
      <li><svg viewBox="0 0 20 20"><circle cx="10" cy="10" r="8.5"/><path d="M1.5 10h17M10 1.5v17M10 1.5c-4 4.5-4 12.5 0 17M10 1.5c4 4.5 4 12.5 0 17M3.5 5.5h13M3.5 14.5h13" fill="none" stroke="#fff" stroke-width="1"/></svg>www.ridgewaynetworks.com.au</li>
    </ul>

    <span class="footer-rule"></span>
    <div class="footer-band">
      <p class="tagline">COMPLETE IT MANAGEMENT</p>
    </div>
  </section>

  <section class="card card--back" aria-label="Card back">
    <div class="brand">
      <span class="brand__square"></span>
      <span class="brand__name">Ridgeway Networks</span>
    </div>
    <p class="web">www.ridgewaynetworks.com.au</p>
  </section>

</main>
</body>
</html>
```